Redesign two existing website pages and one new landing page for dental office

I need to redesign two webpages on my dental website, the Home page (http://velbridgedental.com) and the Dental Implant Services page (http://www.velbridgedental.com/dental-implant-services) and also create a landing page for the Dental Implant Services page.

Please use the same color scheme, slogans and subtitles for the redesign pages and create a reserved video spot on each page. The video spots should not be too big but not too small either and positioned in a central key location on each of the pages. The final redesigned pages should communicate leadership, confidence and trust.

The new landing page for the Dental implant Services page must not have any hyperlinks on the page and must entice the viewer to give name and email before downloading a "Free" eBook called "Is a Fuller Smile Worth the Wait?" Any added photo images to this new page must be smiling.
Updates

Project Deadline Extended Reason: I got feedback that my project was not long enough so I'm extending it by 5 days. Added Thursday, April 16, 2015

Target Market(s)

People who are middle-age to seniors.

Industry/Entity Type

Dental

Coding

Coded - Design and coding required

Number of Pages Required

3 page

Requirements
Must have
• Compatible with existing website colors and theme.

```html
<!DOCTYPE html>
<html lang="en">
<head>
<meta charset="utf-8">
<title>Free eBook Download</title>
<link href="https://fonts.googleapis.com/css2?family=Raleway:wght@600;700&display=swap" rel="stylesheet">
<style>
:root{
  --page-bg:#333333;
  --card-bg:#ffffff;
  --heading:#555555;
  --accent:#3b5a50;
  --label:#333333;
  --field-border:#dddddd;
  --placeholder:#999999;
  --button-text:#ffffff;
}
*{box-sizing:border-box;margin:0;padding:0}
html,body{width:1200px;height:840px;overflow:hidden}
body{background:var(--page-bg);position:relative;font-family:Arial,Helvetica,sans-serif}
.signup-card{
  position:absolute;left:179px;top:155px;width:840px;height:518px;
  background:var(--card-bg);border-radius:6px;
}
.signup-title{
  position:absolute;left:0;right:0;top:38px;text-align:center;
  font-family:"Raleway",sans-serif;font-weight:700;color:var(--heading);
}
.signup-title .line-one{display:block;font-size:30px;line-height:48px}
.signup-title .free{color:var(--accent);font-size:44px;letter-spacing:1px}
.signup-title .line-two{display:block;font-size:35px;line-height:32px}
.field-row{position:absolute;left:0;width:840px;height:53px}
.field-row.name{top:178px}
.field-row.email{top:254px}
.field-label{
  position:absolute;top:16px;
  font-weight:700;font-size:16px;color:var(--label);white-space:nowrap;letter-spacing:.3px;
}
.field-row.name .field-label{right:546px}
.field-row.email .field-label{right:543px}
.field-input{
  position:absolute;left:308px;top:0;width:358px;height:53px;
  border:1px solid var(--field-border);border-radius:5px;
  font-size:17px;color:var(--placeholder);padding:0 14px;font-family:Arial,Helvetica,sans-serif;
}
.field-input::placeholder{color:var(--placeholder)}
.download-button{
  position:absolute;left:185px;top:375px;width:472px;height:67px;
  background:var(--accent);border:0;border-radius:9px;color:var(--button-text);
  font-family:"Raleway",sans-serif;font-weight:700;font-size:22px;
}
.download-button .label{position:absolute;left:116px;top:20px}
.download-button svg{position:absolute;left:400px;top:15px}
</style>
</head>
<body>
<section class="signup-card">
  <h1 class="signup-title">
    <span class="line-one">Download <span class="free">FREE</span>" eBook called</span>
    <span class="line-two">"Is a Fuller Smile Worth the Wait?</span>
  </h1>
  <div class="field-row name">
    <label class="field-label" for="username">Username :</label>
    <input class="field-input" id="username" type="text" placeholder="Your Name">
  </div>
  <div class="field-row email">
    <label class="field-label" for="email">Email Address :</label>
    <input class="field-input" id="email" type="email" placeholder="  Your Email">
  </div>
  <button class="download-button" type="submit">
    <span class="label">Free Download EBook</span>
    <svg width="50" height="38" viewBox="0 0 50 38" fill="none" stroke="#ffffff" stroke-width="2.2" stroke-linejoin="round">
      <path d="M25 5 C19 2 10 2 4 4 V31 C10 29 19 29 25 32 Z"/>
      <path d="M25 5 C31 2 40 2 46 4 V31 C40 29 31 29 25 32 Z"/>
      <path d="M1 8 V35 H20 C22 35 24 36 25 36 C26 36 28 35 30 35 H49 V8"/>
    </svg>
  </button>
</section>
</body>
</html>
```